Design and Renovation Company Luxury Business Card

I want to create a luxury business card for a Design and Renovation Firm . We will use our current logo. The company name is 528BUILDA. We do not want anything standard. We need a very unique concept.
Please see uploaded inspiration. I really like the textured paper option. I would like the card to be thick with debossing, and/or embossing options. The logo has orange in it but I would like to see the card with and without the orange. I think the orange may make the company feel less high-end. The goal is to elevate the logo not match its vibe per se of the logo. We want something very unique, not standard at all!
I would like a space for :
Logo,
Name,
Position,
Email,
Office number,
Website Address,
Business Address,
Thank you!
Have fun!
Target Market(s)
Home owners Age 35 +
Industry/Entity Type
Design and Renovation
Contact Information for Business Card
Logo, Name, Position, Email, Office number, Website Address, Business Address,.
Colors
Designer to choose colors to be used in the design.
Requirements
Must have
- A luxury designer feel. Must be black or dark grey but open to other luxury ideas.
Nice to have
- Gold, silver, black embossing or debossing. Textured paper design.
Should not have
- A cheap look and feel.

```html
<!DOCTYPE html>
<html lang="en">
<head>
<meta charset="utf-8">
<title>528BUILDA Business Card</title>
<link href="https://fonts.googleapis.com/css2?family=Roboto:wght@400;500&display=swap" rel="stylesheet">
<style>
  :root {
    --page: #0c0c0c;
    --card: #151515;
    --card-edge: #1d1d1d;
    --tile-dark: #121212;
    --tile-light: #262626;
    --gold: #dcc48e;
  }
  * { margin: 0; padding: 0; box-sizing: border-box; }
  html, body {
    width: 1200px; height: 900px; overflow: hidden;
    background: var(--page);
    font-family: "Roboto", Arial, sans-serif;
  }
  .canvas {
    position: relative; width: 1200px; height: 900px;
    display: flex; flex-direction: column; align-items: center; justify-content: center; gap: 40px;
  }
  .card {
    position: relative; width: 620px; height: 354px;
    background: radial-gradient(ellipse at 30% 20%, var(--card-edge), var(--card) 70%);
    box-shadow: 0 18px 40px rgba(0,0,0,.7);
  }
  .card-back .tile-field {
    position: absolute; inset: 0;
    background: linear-gradient(135deg, var(--tile-light), var(--tile-dark) 55%, var(--tile-light));
    opacity: .85;
  }
  .card-back .back-brand {
    position: absolute; right: 44px; bottom: 40px;
    display: flex; align-items: center; gap: 8px;
    color: var(--gold); font-size: 14px; font-weight: 400; letter-spacing: 1px;
  }
  .brand-dot { display: inline-block; border-radius: 50%; background: var(--gold); flex: none; }
  .back-brand .brand-dot { width: 8px; height: 8px; }

  .card-front .identity { position: absolute; left: 58px; top: 54px; color: var(--gold); }
  .person-name { font-size: 25px; font-weight: 500; letter-spacing: .3px; line-height: 1; }
  .person-role { font-size: 17px; font-weight: 400; margin-top: 4px; }
  .address {
    position: absolute; left: 76px; top: 138px;
    color: var(--gold); font-size: 17px; line-height: 1.3; font-style: normal;
  }
  .contacts { position: absolute; left: 76px; top: 216px; list-style: none; color: var(--gold); font-size: 17px; }
  .contacts li { display: flex; align-items: center; gap: 12px; line-height: 26px; }
  .contacts svg { width: 18px; height: 18px; flex: none; }
  .brand {
    position: absolute; right: 44px; bottom: 66px;
    color: var(--gold); text-align: right;
  }
  .brand-line { display: flex; align-items: center; justify-content: flex-end; gap: 10px; }
  .brand .brand-dot { width: 12px; height: 12px; }
  .brand-name { font-size: 34px; font-weight: 400; letter-spacing: 2px; line-height: 1; }
  .brand-tagline { font-size: 11px; font-weight: 400; letter-spacing: 1.2px; margin-top: 6px; }
</style>
</head>
<body>
<main class="canvas">
  <section class="card card-back">
    <div class="tile-field" role="img" aria-label="Embossed mosaic tile pattern in dark greys"></div>
    <div class="back-brand"><span class="brand-dot"></span>528BUILDA</div>
  </section>

  <section class="card card-front">
    <div class="identity">
      <p class="person-name">MARCUS HALE</p>
      <p class="person-role">Managing Director</p>
    </div>
    <address class="address">
      87, Harbour Lane Works<br>60318, Country Name
    </address>
    <ul class="contacts">
      <li>
        <svg viewBox="0 0 24 24" fill="none" stroke="currentColor" stroke-width="2"><path d="M5 3h4l2 5-2.5 1.5a11 11 0 0 0 6 6L16 13l5 2v4a2 2 0 0 1-2 2A16 16 0 0 1 3 5a2 2 0 0 1 2-2z"/></svg>
        044-987 654 321
      </li>
      <li>
        <svg viewBox="0 0 24 24" fill="none" stroke="currentColor" stroke-width="2"><rect x="3" y="5" width="18" height="14"/><path d="M3 5l9 7 9-7"/></svg>
        info@studioname.com
      </li>
      <li>
        <svg viewBox="0 0 24 24" fill="none" stroke="currentColor" stroke-width="1.8"><circle cx="12" cy="12" r="9"/><ellipse cx="12" cy="12" rx="4" ry="9"/><path d="M3 12h18M5 7h14M5 17h14"/></svg>
        www.studioname.com
      </li>
    </ul>
    <div class="brand">
      <div class="brand-line">
        <span class="brand-dot"></span>
        <p class="brand-name">528BUILDA</p>
      </div>
      <p class="brand-tagline">Design and Renovation Firm</p>
    </div>
  </section>
</main>
</body>
</html>
```